Newsletter Design Project

I need a new design for a monthly newsletter that I do for Kestrelwood Learning Collective Brisbane. I have been doing the same thing since 2009. We are based in Brisbane and we run classes for semi retired and retired people. I write about social activities, class activities, vacancies etc. I take photos and include them we hhave a logo that I always use. and would just like the newsletter to look different and fresh. The logo is Blue

```html
<!DOCTYPE html>
<html lang="en">
<head>
<meta charset="utf-8">
<title>Kestrelwood Learning Collective Brisbane – E Newsletter May 2013</title>
<link href="https://fonts.googleapis.com/css2?family=Noto+Sans:wght@400;700&family=Jost:wght@500&display=swap" rel="stylesheet">
<style>
:root{
  --navy:#0a0a6e;
  --blue:#3a48f0;
  --mid:#5d7cf2;
  --sky:#6f93f7;
  --lilac:#c9c9fa;
  --panel:#cccdfb;
  --ink:#111133;
  --white:#ffffff;
}
*{box-sizing:border-box;margin:0;padding:0}
html,body{width:816px;height:1200px;overflow:hidden;background:var(--white)}
body{font-family:"Noto Sans",Verdana,sans-serif;color:var(--ink);position:relative}
.tile{position:absolute;z-index:0}
.tile.navy{background:var(--navy)}
.tile.blue{background:var(--blue)}
.tile.mid{background:var(--mid)}
.tile.sky{background:var(--sky)}
.tile.lilac{background:var(--lilac)}
.round-tl{border-top-left-radius:26px}
.round-tr{border-top-right-radius:26px}
.round-bl{border-bottom-left-radius:26px}
.round-br{border-bottom-right-radius:26px}

.brand{position:absolute;left:0;width:816px;top:92px;text-align:center}
.brand-mark{display:inline-flex;align-items:center;gap:10px;font-weight:700;font-size:44px;color:var(--blue);line-height:1}
.brand-mark .dot{width:26px;height:26px;border-radius:50%;background:var(--navy)}
.brand-tag{font-size:10px;font-style:italic;color:var(--navy);margin-top:4px}
.brand-name{font-size:13px;font-weight:700;font-style:italic;color:var(--navy);margin-top:2px}

.masthead{position:absolute;top:194px;left:0;width:816px;text-align:center;font-size:54px;font-weight:700;color:var(--navy);line-height:1}
.issue{position:absolute;top:250px;left:238px;width:328px;height:36px;background:var(--blue);color:var(--white);font-family:"Jost",sans-serif;font-size:28px;text-align:center;line-height:36px}

.panel{position:absolute;top:298px;left:0;width:816px;height:368px;background:var(--panel);padding:10px 0 0 70px}
.section-title{display:flex;align-items:center;gap:12px;font-weight:700;color:var(--navy);line-height:1.1}
.section-title .plus{width:16px;height:16px;flex:none}
.section-title.lg{font-size:32px}
.section-title.sm{font-size:21px}
.panel p{font-size:14.5px;line-height:1.4;color:var(--ink)}
.panel .body{margin-left:-5px}
.term{margin-bottom:14px}
.president{margin-bottom:30px}

.district-title{position:absolute;top:680px;left:70px;font-size:23px}
.entry-label{position:absolute;z-index:2;left:60px;height:30px;width:460px;font-size:17px;font-weight:700;color:var(--navy);line-height:30px;padding-left:6px;background:linear-gradient(90deg,#d9ddfb,#ffffff)}
.entry-label span{color:var(--sky)}
.entry-body{position:absolute;z-index:2;left:55px;width:580px;background:var(--navy);color:var(--white);font-size:14.5px;line-height:1.38;padding:8px 10px 14px 12px}
.photo-frame{position:absolute;z-index:2;background:var(--navy);border-radius:14px;padding:8px}
.photo-frame .photo{width:100%;height:100%;border-radius:10px}
.photo.wynnum{background:linear-gradient(160deg,#c9c4c0,#8d7d77 60%,#5e4c44)}
.photo.logan{background:linear-gradient(170deg,#c7b39f,#a0725a 55%,#6b4635)}
</style>
</head>
<body>
<div class="tile navy round-bl" style="left:6px;top:0;width:62px;height:74px"></div>
<div class="tile mid" style="left:82px;top:0;width:68px;height:74px"></div>
<div class="tile lilac" style="left:162px;top:0;width:70px;height:74px"></div>
<div class="tile sky" style="left:244px;top:0;width:70px;height:74px"></div>
<div class="tile lilac" style="left:326px;top:0;width:70px;height:74px"></div>
<div class="tile lilac" style="left:408px;top:0;width:62px;height:74px"></div>
<div class="tile navy" style="left:486px;top:0;width:60px;height:74px"></div>
<div class="tile lilac round-tl" style="left:28px;top:162px;width:54px;height:76px"></div>
<div class="tile lilac" style="left:620px;top:88px;width:76px;height:68px"></div>
<div class="tile navy round-tr" style="left:704px;top:88px;width:72px;height:74px"></div>
<div class="tile mid" style="left:704px;top:170px;width:72px;height:76px"></div>
<div class="tile lilac" style="left:0;top:724px;width:48px;height:62px"></div>
<div class="tile lilac" style="left:0;top:842px;width:48px;height:72px"></div>
<div class="tile lilac" style="left:0;top:960px;width:48px;height:72px"></div>
<div class="tile navy round-tr" style="left:0;top:1090px;width:64px;height:66px"></div>
<div class="tile navy" style="left:120px;top:1090px;width:68px;height:62px"></div>
<div class="tile mid" style="left:200px;top:1090px;width:70px;height:62px"></div>
<div class="tile blue" style="left:280px;top:1090px;width:70px;height:62px"></div>
<div class="tile lilac" style="left:372px;top:1090px;width:70px;height:62px"></div>
<div class="tile blue" style="left:456px;top:1090px;width:70px;height:62px"></div>
<div class="tile lilac" style="left:540px;top:1090px;width:70px;height:62px"></div>
<div class="tile navy round-tl" style="left:120px;top:1162px;width:70px;height:38px"></div>
<div class="tile lilac" style="left:200px;top:1162px;width:68px;height:38px"></div>
<div class="tile mid" style="left:372px;top:1162px;width:70px;height:38px"></div>
<div class="tile mid" style="left:456px;top:1162px;width:70px;height:38px"></div>
<div class="tile lilac" style="left:540px;top:1162px;width:70px;height:38px"></div>
<div class="tile mid" style="left:630px;top:1162px;width:76px;height:38px"></div>
<div class="tile lilac" style="left:720px;top:1162px;width:70px;height:38px"></div>

<header>
  <div class="brand">
    <div class="brand-mark"><span class="dot"></span>KLC</div>
    <div class="brand-tag">Courses you've always wanted to do</div>
    <div class="brand-name">Kestrelwood Learning Collective Brisbane</div>
  </div>
  <h1 class="masthead">E Newsletter</h1>
  <div class="issue">May 2013</div>
</header>

<section class="panel">
  <h2 class="section-title lg"><svg class="plus" viewBox="0 0 16 16"><rect width="16" height="16" fill="#0a0a6e"/><rect x="3" y="7" width="10" height="2" fill="#fff"/><rect x="7" y="3" width="2" height="10" fill="#fff"/></svg>Term 2:</h2>
  <div class="body term"><p>Did you realise that we are nearly half way through this term? 2013 seems to be racing</p></div>

  <h2 class="section-title lg"><svg class="plus" viewBox="0 0 16 16"><rect width="16" height="16" fill="#0a0a6e"/><rect x="3" y="7" width="10" height="2" fill="#fff"/><rect x="7" y="3" width="2" height="10" fill="#fff"/></svg>Message from the President:</h2>
  <div class="body president"><p>Alan says “I have access to a large group of book publishers—<br>Harbour Books, Wexley, RB Press, Southgate Press and many more— who would like older<br>people to review their latest books. These include fiction, non fiction and poetry.”<br>If you would like to write a book review (and keep the new publications as your own) please<br>contact the President, Alan Merrow at amerrow@kestrelmail.com.au</p></div>

  <h2 class="section-title sm"><svg class="plus" viewBox="0 0 16 16"><rect width="16" height="16" fill="#0a0a6e"/><rect x="3" y="7" width="10" height="2" fill="#fff"/><rect x="7" y="3" width="2" height="10" fill="#fff"/></svg>Bus Review from the Moreton City Council. The link is as follows:</h2>
  <div class="body" style="margin-top:10px"><p>http//www.moretoncitycouncil.org.au/transport/public-transport/buses/bus-network-<br>review/index.htm<br>This will allow you to assess if you need to object to any of the changes.</p></div>
</section>

<h2 class="section-title sm district-title"><svg class="plus" viewBox="0 0 16 16"><rect width="16" height="16" fill="#0a0a6e"/><rect x="3" y="7" width="10" height="2" fill="#fff"/><rect x="7" y="3" width="2" height="10" fill="#fff"/></svg>District information:</h2>

<article>
  <div class="entry-label" style="top:714px"><span>Wynnum:</span> from Margaret Hale</div>
  <div class="entry-body" style="top:746px;height:126px">“Our Wynnum Calligraphy Group recently celebrated the 80th birthday of one of our long time members, Josie Dawson. We had a special morning tea after our Calligraphy class complete with birthday cake and a Birthday Tiara for Josie.”</div>
  <div class="photo-frame" style="left:652px;top:706px;width:124px;height:174px"><div class="photo wynnum" role="img" aria-label="Photo of the Wynnum member cutting her 80th birthday cake"></div></div>
</article>

<article>
  <div class="entry-label" style="top:920px"><span>Logan:</span> from Joan Pemberton</div>
  <div class="entry-body" style="top:952px;height:124px;width:575px">“Logan District students are sad that we will soon lose Beatrice Rowe who has taught Spanish in her inimitable style to hundreds of students in the city and in Logan. Bea is moving to Victoria Point at the end of May and plans to teach Spanish for Redlands KLC. Our loss is their gain and we hope Bea will be very happy in her new home. Meanwhile students are hoping to find another tutor.”</div>
  <div class="photo-frame" style="left:654px;top:928px;width:152px;height:174px"><div class="photo logan" role="img" aria-label="Portrait photo of the departing Spanish tutor"></div></div>
</article>
</body>
</html>
```